Brindle Barks Chews Pouch Design

I want a pouch design for my yak cheese dog chews. My competitor is kindly tail, see attached. I want something minimalist like that where you see that there is only 3 ingredients, Yak milk, lime juice, Himalayan salt. I want it to say 100% natural 100% organic on it. Also odor free. There has to be a big see through window on it so you can see the products inside. Here is my logo and my competitor package. The package is 13cm x 17cm x 5cm. I have 5 sizes of bags to create but same image design
Updates

Target Market(s)

Pet owners

Industry/Entity Type

Dog products

Requirements
Must have
• « SMALL » « MIN NET WT 200 g / 5 PCS » and its important the 3 ingredients mentioned and 100% natural and organic must be very visible however the window must be big
Should not have
• The ingredients in the back

```html
<!DOCTYPE html>
<html lang="en">
<head>
<meta charset="utf-8">
<title>Brindle Barks Chews – Pouch Front and Back</title>
<link rel="stylesheet" href="https://fonts.googleapis.com/css2?family=Boogaloo&family=Lilita+One&family=Josefin+Sans:ital,wght@0,400;0,600;0,700;1,700&display=swap">
<style>
:root{
  --backdrop:#fbe69c;
  --kraft:#e8c57a;
  --kraft-edge:#dcb566;
  --gold:#f2b43a;
  --orange:#e2773a;
  --cream:#f8f0d6;
  --rust:#c97a3c;
  --brown:#6b3a24;
  --window-a:#b9b9b7;
  --window-b:#d9d9d6;
}
*{margin:0;padding:0;box-sizing:border-box}
html,body{width:1200px;height:1018px;overflow:hidden;background:var(--backdrop)}
.canvas{position:relative;width:1200px;height:1018px;background:var(--backdrop)}
.pouch{position:absolute;top:194px;width:434px;height:702px;background:var(--kraft);border-radius:18px 18px 2px 2px;overflow:hidden;font-family:"Josefin Sans",sans-serif}
.pouch-front{left:108px}
.pouch-back{left:673px}
.zip-line{position:absolute;left:0;right:0;top:80px;height:2px;background:var(--kraft-edge)}
.band{position:absolute}
.rough{clip-path:polygon(0 6%,8% 0,22% 5%,38% 1%,55% 6%,70% 0,86% 5%,100% 2%,99% 94%,84% 100%,66% 95%,48% 100%,30% 95%,14% 100%,1% 96%)}

/* front */
.window{position:absolute;left:0;top:259px;width:434px;height:198px;background:linear-gradient(100deg,var(--window-a) 0%,var(--window-b) 55%,var(--window-a) 100%)}
.odor-free{left:0;top:133px;width:68px;height:131px;background:var(--gold);display:flex;align-items:center;justify-content:center}
.odor-free span{transform:rotate(90deg);white-space:nowrap;font-family:"Boogaloo",sans-serif;font-size:25px;color:var(--cream);letter-spacing:1px}
.claim-natural{left:138px;top:149px;width:296px;height:46px;background:var(--cream);font-family:"Lilita One",sans-serif;font-size:29px;color:var(--rust);display:flex;align-items:center;justify-content:center;letter-spacing:1px}
.claim-organic{left:141px;top:197px;width:293px;height:48px;background:var(--orange);font-family:"Lilita One",sans-serif;font-size:29px;color:var(--cream);display:flex;align-items:center;justify-content:center;letter-spacing:1px}
.size-tag{left:309px;top:245px;width:125px;height:37px;background:var(--gold);font-family:"Lilita One",sans-serif;font-size:23px;color:var(--orange);display:flex;align-items:center;justify-content:center;letter-spacing:1.5px}
.ingredients-panel{left:0;top:451px;width:434px;height:192px;background:var(--gold)}
.brand-mark{position:absolute;left:31px;top:448px;width:200px;text-align:center}
.brand-mark .dot{display:block;width:96px;height:96px;margin:0 auto 6px;border-radius:50%;background:var(--cream)}
.brand-mark .name{display:block;font-family:"Boogaloo",sans-serif;font-size:26px;line-height:1;color:var(--brown)}
.ingredient-count{position:absolute;left:222px;top:476px;width:180px;text-align:center;font-family:"Lilita One",sans-serif;font-size:14px;color:var(--orange);letter-spacing:.5px}
.ingredient{position:absolute;left:222px;width:180px;text-align:center;white-space:nowrap;font-family:"Boogaloo",sans-serif;color:var(--cream);line-height:1;transform-origin:center top}
.ingredient-main{top:491px;font-size:52px;transform:scaleY(1.45)}
.ingredient-salt{top:556px;font-size:25px;transform:scaleY(1.25)}
.ingredient-lime{top:582px;font-size:44px;transform:scaleY(1.3)}
.net-weight{left:0;top:638px;width:434px;height:64px;background:var(--orange);font-family:"Lilita One",sans-serif;font-size:26px;color:var(--cream);display:flex;align-items:center;justify-content:center;letter-spacing:1px}

/* back */
.story{left:3px;width:424px;text-align:center;padding:0 28px}
.story h2{font-size:13px;font-weight:700;margin-bottom:3px}
.story p{font-size:9.6px;line-height:1.36}
.story-en{top:151px;height:104px;background:var(--cream);color:var(--orange);padding-top:18px}
.story-fr{top:252px;height:104px;background:var(--orange);color:var(--cream);padding-top:16px}
.story-fr p{text-align:justify;text-align-last:center}
.cautions{position:absolute;left:11px;top:355px;width:186px;height:182px;background:var(--gold);border-radius:0 0 12px 12px;padding:10px 12px;color:var(--cream)}
.cautions h3{font-size:12px;font-weight:700;text-align:center;margin:2px 0 3px}
.cautions ul{list-style:none;font-size:7.4px;line-height:1.6}
.nutrition{position:absolute;left:208px;top:363px;width:206px;height:174px;border:2px solid var(--cream);color:var(--cream)}
.nutrition h3{font-size:11.5px;font-weight:700;padding:6px 6px 4px;border-bottom:2px solid var(--cream)}
.nutrition .head{display:flex;justify-content:space-between;font-size:5.5px;line-height:1.2;padding:3px 5px;border-bottom:2px solid var(--cream)}
.nutrition .head span:last-child{text-align:right}
.nutrition table{width:100%;border-collapse:collapse;font-size:8px;font-weight:600}
.nutrition td{padding:0 5px;height:20.6px;border-bottom:1px solid var(--cream)}
.nutrition tr:last-child td{border-bottom:0}
.nutrition td:last-child{text-align:right}
.recipe{position:absolute;left:9px;top:548px;width:405px;height:83px;border:2px solid var(--orange);border-radius:10px;background:rgba(248,240,214,.35);color:var(--orange)}
.recipe h3{font-family:"Lilita One",sans-serif;font-size:15px;font-weight:400;text-align:center;letter-spacing:1px;margin-top:3px}
.steps{display:flex;list-style:none;padding:0 8px;gap:6px}
.steps li{flex:1;display:flex;flex-direction:column;align-items:center}
.steps .line{display:flex;gap:3px;align-items:flex-start}
.steps .num{font-family:"Lilita One",sans-serif;font-size:12px}
.steps .text{font-size:6.8px;font-weight:700;font-style:italic;line-height:1.3}
.steps svg{margin-top:4px}
</style>
</head>
<body>
<main class="canvas">

  <section class="pouch pouch-front" aria-label="Pouch front">
    <div class="zip-line"></div>
    <div class="window" role="img" aria-label="Clear see-through window showing the chews inside"></div>
    <div class="band odor-free"><span>ODOR FREE</span></div>
    <div class="band claim-natural rough">100% NATURAL</div>
    <div class="band claim-organic rough">100%ORGANIC</div>
    <div class="band size-tag">SMALL</div>
    <div class="band ingredients-panel rough"></div>
    <div class="brand-mark">
      <span class="dot"></span>
      <span class="name">Brindle Barks<br>Chews</span>
    </div>
    <div class="ingredient-count">3 INGREDIENTS</div>
    <div class="ingredient ingredient-main">YAK MILK</div>
    <div class="ingredient ingredient-salt">HIMALAYAN SALT</div>
    <div class="ingredient ingredient-lime">LIME JUICE</div>
    <div class="band net-weight">MIN NET WT 200G / 5PCS</div>
  </section>

  <section class="pouch pouch-back" aria-label="Pouch back">
    <div class="zip-line"></div>
    <div class="band story story-en rough">
      <h2>About us:</h2>
      <p>At Brindle Barks Chews, we believe that dogs deserve the best. That's why our chews are made with 100% natural, organic ingredients, ensuring your dog enjoys a healthy, delicious treat. With a focus on quality, we aim to provide a product that reflects our love for dogs and our dedication to their health and happiness.</p>
    </div>
    <div class="band story story-fr rough" lang="fr">
      <h2>Qui sommes-nous:</h2>
      <p>Chez Brindle Barks Chews, nous croyons que les chiens méritent le meilleur. C'est pourquoi nos gâteries sont fabriquées à partir d'ingrédients 100% naturels et biologiques, garantissant un régal sain et délicieux pour votre chien. Nous visons à offrir un produit de qualité qui reflète notre amour pour les chiens et notre dévouement envers leur santé et leur bonheur.</p>
    </div>

    <div class="cautions">
      <h3>Cautions:</h3>
      <ul>
        <li>• Not for human consumption.</li>
        <li>• Supervise pets while giving any treats.</li>
        <li>• Wash hands after handling.</li>
        <li>• Remove treat if product breaks into sharp pieces.</li>
      </ul>
      <h3 lang="fr">Mises en garde:</h3>
      <ul lang="fr">
        <li>• Pour consommation animale seulement.</li>
        <li>• Surveillez vos amis poilus lorsqu'ils grugent des gâteries.</li>
        <li>• Lavez-vous les mains après manipulation.</li>
        <li>• Retirez la gâterie si le produit se casse en morceaux pointus.</li>
      </ul>
    </div>

    <div class="nutrition">
      <h3>Nutrition Facts/Valeur Nutritive</h3>
      <div class="head"><span>Amount<br>Teneur</span><span>%Daily Amount<br>%Valeur quotidienne</span></div>
      <table>
        <tr><td>Energy Level</td><td>355 KCAL/100G</td></tr>
        <tr><td>Crude Protein</td><td>65% Min</td></tr>
        <tr><td>Crude Fat</td><td>1% Min</td></tr>
        <tr><td>Carbohydrates</td><td>10%</td></tr>
        <tr><td>Ashes</td><td>10% Max</td></tr>
        <tr><td>Moisture</td><td>10% Max</td></tr>
      </table>
    </div>

    <div class="recipe">
      <h3>CRUNCHY PUFF RECIPE</h3>
      <ol class="steps">
        <li><div class="line"><span class="num">1.</span><span class="text">Remove the Chewed down end piece</span></div>
          <svg width="22" height="22" viewBox="0 0 22 22" fill="none" stroke="currentColor" stroke-width="1.6"><path d="M4 7l7-4 7 4v9l-7 4-7-4z M4 7l7 4 7-4 M11 11v9"/></svg></li>
        <li><div class="line"><span class="num">2.</span><span class="text">Soak in warm water for 5 minutes.</span></div>
          <svg width="44" height="22" viewBox="0 0 44 22"><path d="M2 4h40c0 9-9 16-20 16S2 13 2 4z" fill="currentColor"/><rect x="17" y="6" width="10" height="9" fill="none" stroke="#f8f0d6" stroke-width="1.4"/></svg></li>
        <li><div class="line"><span class="num">3.</span><span class="text">Microwave for 30 seconds.</span></div>
          <svg width="36" height="24" viewBox="0 0 36 24" fill="none" stroke="currentColor" stroke-width="1.6"><rect x="1" y="1" width="34" height="22" rx="2"/><rect x="5" y="5" width="20" height="14"/><path d="M29 6v3M29 12v3"/></svg></li>
        <li><div class="line"><span class="num">4.</span><span class="text">Let it cool for 2 minutes, then serve to your dog as a crunchy treat!</span></div>
          <svg width="22" height="22" viewBox="0 0 22 22" fill="none" stroke="currentColor" stroke-width="1.6"><path d="M5 10l6-3 6 3v7l-6 3-6-3z M5 10l6 3 6-3 M11 13v7 M8 2v3 M11 1v3 M14 2v3"/></svg></li>
      </ol>
    </div>
  </section>

</main>
</body>
</html>
```